Business Cards for IT Consulting Company (Managed Service Provider)

I am looking to have some business cards printed and would like some designs. We are an IT Consulting company based in Vancouver BC. I would like a nice clean and modern look to the cards. I have uploaded all the versions of my logo so parts can be used as needed. Here is a snippit from our website homepage:

Quillbrook Networks Ltd. is an IT Solutions Partner located in Vancouver BC, Canada. We offer IT solutions and support to customers in the greater Vancouver Area. With expertise in Microsoft platforms, as well as Linux and Mac OSX and over 12 years experience in the IT industry, Quillbrook Networks is dedicated to offering our clients top quality service and products. We take pride in the solutions we offer our customers. The greatest compliment a client can give us is to recommend our services.

Quillbrook Networks Ltd. offers a wide range of IT services from onsite service to remote support and managed service solutions. This allows clients to choose the support path that best suits their company’s needs. Supporting many different sized companies from small to enterprise level over the past 12 years Quillbrook Networks has the experience and expertise needed to ensure things run smoothly. Allowing our clients to focus on doing business.

Revolutionizing the way IT services are delivered.

Quillbrook Networks is dedicated to providing our clients with IT solutions that work and grow with them for years to come. This philosophy helps save money in the long run instead of replacing equipment constantly. Far too often IT solutions are not well thought out and while possibly solving the problem at hand, require replacement due to growth or quality within a very short time frame. Quillbrook Networks takes pride in providing solutions that will last and be able to accommodate growth without the need for replacement.

Industry/Entity Type

Information Technology

Contact Information for Business Card

Quillbrook Networks Ltd.
(Employee Name)
Eml: (Employees Email Address)
Web: quillbrook.me
Ph: 604-555-0148

Font styles to use
Serif
Sans Serif

Requirements
Must have
• The Company logo and company colors.
Nice to have
• - Our tag line: "Revolutionizing IT Services" or "Revolutionizing the way IT services are delivered."
• - Also I really like the idea of nature and technology together blending which is sort of where my logo came from so integrating that somehow onto the business cards would be great.

```html
<!DOCTYPE html>
<html lang="en">
<head>
<meta charset="utf-8">
<title>Quillbrook Networks Ltd. – Business Cards</title>
<link href="https://fonts.googleapis.com/css2?family=Montserrat:wght@600&family=Open+Sans:wght@400;600&display=swap" rel="stylesheet">
<style>
  :root {
    --backdrop: #b9b9b9;
    --card-dark: #050505;
    --card-mid: #1c1c1c;
    --white: #ffffff;
    --grey-rule: #9a9a9a;
    --brand-blue: #1ba3e0;
    --text-light: #f2f2f2;
  }
  * { margin: 0; padding: 0; box-sizing: border-box; }
  html, body {
    width: 1200px; height: 900px; overflow: hidden;
    background: var(--backdrop);
  }
  .canvas {
    position: relative; width: 1200px; height: 900px;
  }
  .card {
    position: absolute; left: 320px; width: 560px; height: 320px;
    background: radial-gradient(ellipse at 50% 40%, var(--card-mid) 0%, var(--card-dark) 75%);
    box-shadow: 0 6px 18px rgba(0,0,0,0.25);
    overflow: hidden;
  }
  .card--back { top: 110px; }
  .card--front { top: 470px; }

  /* Back side */
  .back-brand {
    position: absolute; top: 92px; left: 0; width: 100%;
    display: flex; justify-content: center; align-items: center; gap: 14px;
  }
  .brand-mark {
    width: 18px; height: 18px; border: 2px solid currentColor; border-radius: 50%;
  }
  .brand-name {
    font-family: "Montserrat", sans-serif; font-weight: 600;
    font-size: 30px; letter-spacing: 0.5px; line-height: 1;
  }
  .back-brand { color: var(--white); }
  .tagline-row {
    position: absolute; top: 192px; left: 0; width: 100%;
    display: flex; align-items: center;
  }
  .tagline-row .rule { flex: 1; height: 1px; background: var(--grey-rule); }
  .tagline {
    font-family: "Open Sans", sans-serif; font-weight: 600;
    font-size: 12px; letter-spacing: 1.6px; color: var(--white);
    padding: 0 16px; text-transform: uppercase;
  }

  /* Front side */
  .front-brand {
    position: absolute; top: 46px; left: 44px;
    display: flex; align-items: center; gap: 12px;
    color: var(--brand-blue);
  }
  .front-brand .brand-name { font-size: 28px; }
  .name-row {
    position: absolute; top: 150px; left: 0; width: 100%;
    display: flex; align-items: center;
  }
  .name-row .rule { height: 1px; background: var(--brand-blue); }
  .name-row .rule--long { flex: 1; }
  .name-row .rule--short { width: 28px; }
  .person-name {
    font-family: "Open Sans", sans-serif; font-weight: 600;
    font-size: 19px; color: var(--brand-blue); padding: 0 12px;
  }
  .contact-list {
    position: absolute; top: 190px; right: 36px;
    list-style: none;
    font-family: "Open Sans", sans-serif; font-size: 14px; color: var(--text-light);
  }
  .contact-list li {
    display: flex; justify-content: flex-end; align-items: center;
    gap: 10px; height: 22px;
  }
  .contact-icon { width: 12px; height: 12px; fill: var(--brand-blue); }
</style>
</head>
<body>
<main class="canvas">

  <section class="card card--back" aria-label="Card back">
    <div class="back-brand">
      <span class="brand-mark"></span>
      <span class="brand-name">Quillbrook Networks Ltd.</span>
    </div>
    <div class="tagline-row">
      <span class="rule"></span>
      <span class="tagline">Revolutionizing IT Services</span>
      <span class="rule"></span>
    </div>
  </section>

  <section class="card card--front" aria-label="Card front">
    <div class="front-brand">
      <span class="brand-mark"></span>
      <span class="brand-name">Quillbrook Networks Ltd.</span>
    </div>
    <div class="name-row">
      <span class="rule rule--long"></span>
      <span class="person-name">Daniel Marsh</span>
      <span class="rule rule--short"></span>
    </div>
    <ul class="contact-list">
      <li>604-555-0148
        <svg class="contact-icon" viewBox="0 0 24 24" aria-hidden="true"><path d="M6.6 10.8a15.1 15.1 0 0 0 6.6 6.6l2.2-2.2a1 1 0 0 1 1-.25 11.4 11.4 0 0 0 3.6.57 1 1 0 0 1 1 1V20a1 1 0 0 1-1 1A17 17 0 0 1 3 4a1 1 0 0 1 1-1h3.5a1 1 0 0 1 1 1c0 1.25.2 2.45.57 3.57a1 1 0 0 1-.25 1z"/></svg>
      </li>
      <li>info@quillbrook.me
        <svg class="contact-icon" viewBox="0 0 24 24" aria-hidden="true"><path d="M2 5h20v14H2z M2 5l10 8 10-8" fill="none" stroke="#1ba3e0" stroke-width="2.4"/></svg>
      </li>
      <li>www.quillbrook.me
        <svg class="contact-icon" viewBox="0 0 24 24" aria-hidden="true"><circle cx="12" cy="12" r="10"/><path d="M2 12h20M12 2c3 3 3 17 0 20M12 2c-3 3-3 17 0 20" fill="none" stroke="#050505" stroke-width="1.6"/></svg>
      </li>
    </ul>
  </section>

</main>
</body>
</html>
```